Design a New Business Card for Our Company

We are looking for fresh, unique, and a modern business card that reflects our roots as digital marketing agency focused on SEM.

Industry/Entity Type

Marketing

Contact Information for Business Card

looking for very unique out of the box designs. clean and modern that compliments our logo

Requirements
Must have
• colors should match our logo
• Front should have name, address, email, and phone/fax of the person, phone/fax are the same number
• back should have our url

```html
<!DOCTYPE html>
<html lang="en">
<head>
<meta charset="utf-8">
<title>Nordpeak Solutions – Business Card</title>
<link rel="stylesheet" href="https://fonts.googleapis.com/css2?family=Source+Sans+3:wght@400;600;700&display=swap">
<style>
  :root {
    --backdrop: #ececec;
    --brand-blue: #5d98d2;
    --brand-grey: #a7a7a7;
    --paper: #ffffff;
    --ink-on-blue: #ffffff;
    --rule: #9dbfe3;
  }
  * { box-sizing: border-box; margin: 0; padding: 0; }
  html, body {
    width: 1200px; height: 900px; overflow: hidden;
    background: var(--backdrop);
    font-family: "Source Sans 3", "Myriad Pro", Arial, sans-serif;
  }
  .stage { position: relative; width: 1200px; height: 900px; }

  .card { position: absolute; overflow: hidden; box-shadow: 0 2px 6px rgba(0,0,0,.12); }

  /* Front */
  .card--front {
    left: 238px; top: 62px; width: 555px; height: 343px;
    background: var(--brand-blue); color: var(--ink-on-blue);
  }
  .card__accent { position: absolute; right: -70px; top: -40px; }
  .person { position: absolute; left: 31px; top: 50px; }
  .person__name { font-size: 19px; font-weight: 700; line-height: 1.1; }
  .person__role { font-size: 15px; font-weight: 400; margin-top: 2px; }
  .address { position: absolute; left: 31px; top: 185px; font-size: 15px; line-height: 20px; }
  .contacts { position: absolute; left: 31px; top: 240px; list-style: none; font-size: 15px; line-height: 20px; }
  .contacts li { display: flex; align-items: center; gap: 8px; }
  .contacts svg { width: 12px; height: 12px; fill: var(--ink-on-blue); flex: none; }

  /* Back */
  .card--back {
    left: 458px; top: 519px; width: 560px; height: 342px;
    background: var(--paper);
  }
  .brand {
    position: absolute; left: 96px; top: 118px;
    display: flex; align-items: center; gap: 16px;
    color: var(--brand-blue); font-weight: 600;
  }
  .brand__dot { width: 30px; height: 30px; border-radius: 50%; background: var(--brand-blue); }
  .brand__name { display: flex; flex-direction: column; line-height: 1; }
  .brand__word { font-size: 66px; letter-spacing: -1px; }
  .brand__tagline { font-size: 19px; letter-spacing: 12px; margin-top: 2px; padding-left: 2px; }
  .web {
    position: absolute; left: 0; right: 0; top: 282px;
    display: flex; align-items: center; gap: 14px;
    color: var(--brand-blue); font-size: 16px;
  }
  .web::before, .web::after { content: ""; flex: 1; height: 1px; background: var(--rule); }
</style>
</head>
<body>
<main class="stage">

  <section class="card card--front" aria-label="Business card front">
    <svg class="card__accent" width="200" height="200" viewBox="0 0 200 200" aria-hidden="true">
      <circle cx="100" cy="100" r="78" fill="#ffffff"/>
    </svg>
    <div class="person">
      <p class="person__name">Daniel Hart</p>
      <p class="person__role">Managing Director</p>
    </div>
    <address class="address" style="font-style:normal">
      12345, Address Goes Here<br>
      Country Name, 123456.
    </address>
    <ul class="contacts">
      <li>
        <svg viewBox="0 0 24 24" aria-hidden="true"><path d="M6.6 10.8a15.1 15.1 0 0 0 6.6 6.6l2.2-2.2a1 1 0 0 1 1-.25 11.4 11.4 0 0 0 3.6.57 1 1 0 0 1 1 1V20a1 1 0 0 1-1 1A17 17 0 0 1 3 4a1 1 0 0 1 1-1h3.5a1 1 0 0 1 1 1c0 1.25.2 2.45.57 3.6a1 1 0 0 1-.25 1z"/></svg>
        <span>044-555 010 234</span>
      </li>
      <li>
        <svg viewBox="0 0 24 24" aria-hidden="true"><path d="M7 2h8l2 2v4H7zM4 9h16a2 2 0 0 1 2 2v8a2 2 0 0 1-2 2H4a2 2 0 0 1-2-2v-8a2 2 0 0 1 2-2zm3 4v2h4v-2zm0 3v2h4v-2zm6-3v2h4v-2z"/></svg>
        <span>044-555 010 234</span>
      </li>
      <li>
        <svg viewBox="0 0 24 24" aria-hidden="true"><path d="M2 5h20v14H2zm2 2v.5l8 5 8-5V7l-8 5z"/></svg>
        <span>hello@nordpeak.com</span>
      </li>
    </ul>
  </section>

  <section class="card card--back" aria-label="Business card back">
    <div class="brand">
      <span class="brand__dot" aria-hidden="true"></span>
      <p class="brand__name">
        <span class="brand__word">nordpeak</span>
        <span class="brand__tagline">SOLUTIONS</span>
      </p>
    </div>
    <p class="web">www.nordpeak.com</p>
  </section>

</main>
</body>
</html>
```